International business needs business cards

Our company, DRV Ventures Inc. is in the business of supplying a range construction products with particular emphasis on CEMENT. We have developed our own brand - TORVAN SUPPLIES - with which to infiltrate the market. We are launching our brand of cement (TORVAN Type IS Cement) into the Caribbean which is unlike anything this market has ever seen. A monopoly has existed here for the past 60-odd years and the market has now opened to allow the importation of other brands and consumers are anxious and ready for change/improvement. We are very excited to be launching and want to make a great first impression. We will be conducting workshops and seminars (from government level to the hardware store owners) and we want our business card to give us the strong, confident introduction that we need.

Target Market(s)

construction; builders; engineers; home owners

Industry/Entity Type

Construction

Contact Information for Business Card

Marisol Depree
CEO
cell # 1 555 4180736
Ground floor,Lindell Plaza Suite 2734
George Town,Grand Cayman
Cayman Islands,KY1-4823
EMAIL: m.depree@drvventuresinc.example
web site drvventuresinc.example

COMPANY: skype info drv.ventures.example

second card
Yvette Brannock-Depree
CFO
CELL# 1 555 607 3941
George Town,Grand Cayman
Cayman Islands,KY1-4823
EMAIL: y.brannockdepree@drvventuresinc.example
website drvventuresinc.example

Requirements
Must have
• Business cards must display BOTH logos - DRV is the company and TORVAN is the brand.

```html
<!DOCTYPE html>
<html lang="en">
<head>
<meta charset="utf-8">
<title>DRV Ventures Inc. — Business Card</title>
<link href="https://fonts.googleapis.com/css2?family=Open+Sans:wght@400;600;700&family=Libre+Baskerville:wght@700&display=swap" rel="stylesheet">
<style>
  :root {
    --canvas-bg: #e9e6e2;
    --card-white: #f4f4f4;
    --brand-red: #b01c24;
    --brand-red-dark: #7e1117;
    --ink-black: #111111;
    --text-white: #ffffff;
    --social-muted: #9fb6cf;
  }
  * { margin: 0; padding: 0; box-sizing: border-box; }
  html, body { width: 1200px; height: 780px; overflow: hidden; background: var(--canvas-bg); }
  .canvas { position: relative; width: 1200px; height: 780px; }

  .card {
    position: absolute; top: 235px; width: 540px; height: 310px;
    border-radius: 14px; overflow: hidden;
    box-shadow: 0 8px 22px rgba(0,0,0,.22);
    font-family: "Open Sans", Arial, sans-serif; color: var(--text-white);
  }
  .card--front { left: 40px; background: var(--card-white); }
  .card--back {
    left: 620px;
    background: radial-gradient(ellipse at 55% 55%, var(--brand-red) 0%, var(--brand-red-dark) 100%);
  }
  .card__shapes { position: absolute; inset: 0; }

  .company-mark { position: absolute; left: 36px; top: 88px; display: flex; align-items: center; gap: 12px; }
  .company-mark__square { width: 44px; height: 44px; background: var(--brand-red); }
  .company-mark__name { font-family: "Libre Baskerville", Georgia, serif; font-weight: 700; font-size: 24px; color: var(--ink-black); }

  .social-links { position: absolute; right: 28px; top: 18px; display: flex; gap: 6px; }
  .social-links__item { width: 18px; height: 18px; border-radius: 3px; background: var(--social-muted); }

  .contact { position: absolute; left: 215px; top: 190px; }
  .contact__name { font-weight: 700; font-size: 24px; line-height: 1.15; }
  .contact__role { font-size: 14px; line-height: 1.3; margin-top: 1px; }
  .contact__line { display: flex; align-items: center; gap: 8px; font-size: 13.5px; line-height: 18px; margin-top: 6px; }
  .contact__line:first-of-type { margin-top: 10px; }
  .contact__icon { width: 16px; height: 16px; flex: none; }

  .website { position: absolute; right: 26px; top: 160px; font-size: 15px; }

  .address { position: absolute; left: 28px; top: 24px; font-size: 13px; line-height: 1.55; }
  .brand-mark {
    position: absolute; left: 0; right: 0; top: 150px; text-align: center;
    font-weight: 700; font-size: 46px; letter-spacing: 6px;
  }
</style>
</head>
<body>
<main class="canvas">

  <section class="card card--front" aria-label="Business card front">
    <svg class="card__shapes" viewBox="0 0 540 310" aria-hidden="true">
      <path d="M58,310 C108,226 190,138 326,128 C428,120 498,104 540,82 L540,310 Z" fill="var(--ink-black)"/>
      <path d="M74,310 C124,232 204,150 332,140 C432,132 500,118 540,98 L540,310 Z" fill="var(--card-white)"/>
      <path d="M80,310 C130,236 210,156 336,146 C436,138 502,124 540,106 L540,310 Z" fill="var(--brand-red)"/>
    </svg>

    <div class="social-links">
      <span class="social-links__item"></span>
      <span class="social-links__item"></span>
    </div>

    <div class="company-mark">
      <span class="company-mark__square"></span>
      <span class="company-mark__name">DRV Ventures Inc.</span>
    </div>

    <div class="website">drvventuresinc.example</div>

    <div class="contact">
      <div class="contact__name">Marisol Depree</div>
      <div class="contact__role">CEO</div>
      <div class="contact__line">
        <svg class="contact__icon" viewBox="0 0 16 16" aria-hidden="true">
          <rect width="16" height="16" rx="3" fill="#fff"/>
          <path d="M5 3.5 L6.8 5.3 L5.9 6.6 C6.6 8 7.9 9.3 9.4 10.1 L10.7 9.2 L12.5 11 L11.3 12.5 C7.6 12 4 8.4 3.5 4.7 Z" fill="var(--brand-red)"/>
        </svg>
        <span>1 555 4180736</span>
      </div>
      <div class="contact__line">
        <svg class="contact__icon" viewBox="0 0 16 16" aria-hidden="true">
          <rect width="16" height="16" rx="3" fill="#fff"/>
          <rect x="3" y="4.5" width="10" height="7" fill="none" stroke="var(--brand-red)" stroke-width="1.3"/>
          <path d="M3 4.5 L8 8.6 L13 4.5" fill="none" stroke="var(--brand-red)" stroke-width="1.3"/>
        </svg>
        <span>m.depree@drvventuresinc.example</span>
      </div>
    </div>
  </section>

  <section class="card card--back" aria-label="Business card back">
    <div class="address">
      Ground floor,Lindell Plaza Suite 2734, George Town,Grand Cayman<br>
      Cayman Islands,KY1-4823
    </div>
    <div class="brand-mark">TORVAN</div>
  </section>

</main>
</body>
</html>
```